New Zealand Marlborough Sauvignon Blanc wine packaging design

We need packaging design for our new wine brand, Dunmore Vale. The wine is a New Zealand Marlborough Sauvignon Blanc. We would like the packaging will portray elegance and style with an understated label. We are looking for a label that portrays the elegance of the French Riviera. The label should be round or pill shaped.
Updates

Industry/Entity Type

Wine

Font styles to use
Serif
Sans Serif

Requirements
Must have
• The words in order of importance: Dunmore Vale, Sauvignon Blanc, Marlborough, New Zealand. It should be fit to the bottle posted in the links
Nice to have
• a pill shape or circular shape
Should not have
• Illustrations of wine bottles, wine glasses, or grapes

```html
<!DOCTYPE html>
<html lang="en">
<head>
<meta charset="utf-8">
<title>Dunmore Vale Sauvignon Blanc Label</title>
<link rel="stylesheet" href="https://fonts.googleapis.com/css2?family=Italiana&display=swap">
<style>
  :root {
    --paper: #ffffff;
    --label-black: #000000;
    --pattern-teal: #052a31;
    --accent-teal: #00a6c8;
    --cream: #ffffff;
  }
  html, body {
    margin: 0;
    padding: 0;
    width: 1200px;
    height: 675px;
    overflow: hidden;
    background: var(--paper);
  }
  .canvas {
    position: relative;
    width: 1200px;
    height: 675px;
    background: var(--paper);
  }
  .label {
    position: absolute;
    left: 0;
    top: 0;
    width: 1200px;
    height: 675px;
  }
  .label-base { fill: var(--label-black); }
  .label-pattern { fill: url(#patternGlow); }
  .ornament-area { fill: url(#ornamentTone); }
  .wave-band { fill: var(--accent-teal); }
  .brand-name {
    font-family: "Italiana", serif;
    font-size: 80px;
    fill: var(--cream);
    letter-spacing: 1px;
  }
  .varietal {
    font-family: "Italiana", serif;
    font-size: 26px;
    fill: var(--accent-teal);
    letter-spacing: 0.5px;
  }
  .region {
    font-family: "Italiana", serif;
    font-size: 15px;
    fill: var(--cream);
    letter-spacing: 0.5px;
  }
  .region-divider {
    stroke: var(--cream);
    stroke-width: 1;
  }
</style>
</head>
<body>
<main class="canvas">
  <svg class="label" viewBox="-600 -337 1200 675" xmlns="http://www.w3.org/2000/svg">
    <defs>
      <clipPath id="labelShape">
        <circle cx="0" cy="0" r="256"/>
      </clipPath>
      <radialGradient id="patternGlow" cx="0" cy="0" r="252" gradientUnits="userSpaceOnUse">
        <stop offset="0" stop-color="#041f25"/>
        <stop offset="0.85" stop-color="#052a31"/>
        <stop offset="1" stop-color="#021519"/>
      </radialGradient>
      <linearGradient id="ornamentTone" x1="0" y1="0" x2="0" y2="1">
        <stop offset="0" stop-color="#00a6c8"/>
        <stop offset="1" stop-color="#0090ae"/>
      </linearGradient>
    </defs>

    <g clip-path="url(#labelShape)">
      <circle class="label-base" cx="0" cy="0" r="256"/>
      <circle class="label-pattern" cx="0" cy="0" r="250" role="img"
              aria-label="Faint dark teal Māori-inspired koru pattern across the label background"/>
      <path class="wave-band" role="img"
            aria-label="Bright teal carved wave ornament sweeping across the lower label"
            d="M -165 270 C -165 175 -70 135 15 135 C 115 135 175 88 262 80 L 262 270 Z"/>
    </g>

    <rect class="ornament-area" x="-48" y="-256" width="96" height="158" rx="10"
          role="img" aria-label="Teal carved pendant ornament at the top of the label"/>

    <text class="brand-name" x="0" y="-18" text-anchor="middle">DUNMORE</text>
    <text class="brand-name" x="-8" y="44" text-anchor="middle">VALE</text>
    <text class="varietal" x="0" y="76" text-anchor="middle">SAUVIGNON BLANC</text>

    <text class="region" x="-10" y="112" text-anchor="end">MARLBOROUGH</text>
    <line class="region-divider" x1="0" y1="98" x2="0" y2="114"/>
    <text class="region" x="10" y="112" text-anchor="start">NEW ZEALAND</text>
  </svg>
</main>
</body>
</html>
```